Graphic Design Project

We make rose petal jelly from old fashioned english roses. The jelly is sweet eaten with scones and clotted cream or as a filling in a victoria sandwich, as a topping on ice cream or thick set yogurt.
The image of the product is luxurious and decadent and very english.
We need a design for a label which has a picture of an old fashioned rose (rosa mundi or a compte de chambard) The rose must stand out clearly so the jelly is not confused with other fruit jams. The overall colour of the label should be pink and soft, with white or dark pink writing. The label needs to be fridge proof.

We also need a security strip to fit on the lid of the jar.

We need the following information on the label.
Name of our company-"Meadow Crown"
Name of Product-"Rose Petal Jelly"
Sales pitch-"With whole petals-a taste of summer, delicious on scones, as a filling in sponge cake, as a topping on ice cream or yogurt."
INGREDIENTS: Sugar, water, rose petals, lemon juice, natural jelling agent (agar-agar)
STORAGE: Store in a cool dry place, once opened keep refrigerated and consume within 4 weeks.
BEST BEFORE: See base

200g
Produced by:
MEADOW CROWN
The Larches
Pardew Lane
Newnham
Gloucestershire
GL17 4RX
The label must have room for a bar code. The size of label approx 8-10cm long 5cm wide.
Updates

Hi

Just been looking at the Hartwell and Brace site and the labels they have there have the up market feel I am trying to convey. Hope that helps, its classy but not twee.

Thanks

Thanks for all submissions. I would be grateful if you googled images for 'Colourful and expensive biscuits at Hartwell Brace' The designs on the tins are the image we are trying to create. The colours are quite strong.

Thanks

Target Market(s)

older well off people who visit garden centres

Industry/Entity Type

Security

Requirements
Must have
• All writen info above and picture of old fashioned rose prferably rose a mundi. Luxury feel, very english, to appeal to older market
Pink colour sheme
Should not have
• dark or manly colours

```html
<!DOCTYPE html>
<html lang="en">
<head>
<meta charset="utf-8">
<title>Meadow Crown – Rose Petal Jelly Label</title>
<link href="https://fonts.googleapis.com/css2?family=Arimo:wght@400;700&family=Crimson+Pro:ital,wght@1,400&family=Tinos&family=Tenor+Sans&display=swap" rel="stylesheet">
<style>
  :root {
    --magenta: #e0137b;
    --band: #e5167f;
    --cream: #fbeedb;
    --paper: #ffffff;
    --ink: #111111;
    --rose-light: #f7c6d3;
    --rose-mid: #ec8fae;
    --leaf: #8fa66a;
  }
  html, body {
    margin: 0;
    padding: 0;
    width: 1200px;
    height: 666px;
    overflow: hidden;
    background: #ffffff;
  }
  .label {
    position: relative;
    width: 1200px;
    height: 666px;
    overflow: hidden;
    background: linear-gradient(90deg, var(--cream) 0%, #fdf6ec 35%, var(--paper) 65%);
  }
  .rose-art {
    position: absolute;
    left: 0;
    top: 0;
    width: 295px;
    height: 478px;
    background:
      radial-gradient(ellipse at 40% 20%, var(--rose-mid) 0%, transparent 45%),
      radial-gradient(ellipse at 55% 55%, var(--rose-light) 0%, transparent 50%),
      radial-gradient(ellipse at 35% 85%, var(--rose-mid) 0%, transparent 45%),
      linear-gradient(90deg, #f4bccb 0%, #f8d6de 55%, rgba(251,238,219,0) 100%);
  }
  .brand-tab {
    position: absolute;
    left: 352px;
    top: 0;
    width: 494px;
    height: 90px;
    background: var(--band);
    border-radius: 0 0 38px 38px;
    color: var(--paper);
    font-family: "Tenor Sans", sans-serif;
    font-size: 38px;
    font-variant: small-caps;
    letter-spacing: 3px;
    text-align: center;
    line-height: 94px;
  }
  .product-name {
    position: absolute;
    left: 240px;
    width: 720px;
    top: 128px;
    margin: 0;
    text-align: center;
    font-family: "Tinos", serif;
    font-weight: 400;
    font-size: 98px;
    line-height: 1;
    color: var(--magenta);
  }
  .sales-pitch {
    position: absolute;
    left: 290px;
    width: 676px;
    top: 268px;
    margin: 0;
    text-align: center;
    font-family: "Crimson Pro", serif;
    font-style: italic;
    font-size: 32px;
    line-height: 48px;
    color: var(--magenta);
  }
  .net-weight {
    position: absolute;
    left: 500px;
    width: 200px;
    top: 440px;
    text-align: center;
    font-family: "Arimo", sans-serif;
    font-size: 23px;
    color: var(--magenta);
  }
  .producer {
    position: absolute;
    left: 1008px;
    top: 24px;
    height: 350px;
    writing-mode: vertical-rl;
    transform: rotate(180deg);
    font-family: "Arimo", sans-serif;
    font-size: 26px;
    line-height: 37px;
    color: var(--magenta);
    margin: 0;
  }
  .divider {
    position: absolute;
    left: 0;
    top: 477px;
    width: 1200px;
    height: 4px;
    background: var(--band);
  }
  .info-band {
    position: absolute;
    left: 0;
    top: 490px;
    width: 1200px;
    height: 176px;
    background: var(--band);
  }
  .product-info {
    position: absolute;
    left: 34px;
    top: 514px;
    margin: 0;
    font-family: "Arimo", sans-serif;
    font-weight: 700;
    font-size: 21.5px;
    line-height: 32.5px;
    color: var(--paper);
  }
  .best-before {
    position: absolute;
    right: 232px;
    top: 570px;
    margin: 0;
    text-align: right;
    font-family: "Arimo", sans-serif;
    font-weight: 700;
    font-size: 21.5px;
    line-height: 29px;
    color: var(--paper);
  }
  .barcode-space {
    position: absolute;
    left: 991px;
    top: 398px;
    width: 181px;
    height: 238px;
    background: var(--paper);
    border: 1.5px solid #555;
    box-sizing: border-box;
    display: flex;
    align-items: center;
    justify-content: center;
  }
  .barcode-space span {
    writing-mode: vertical-rl;
    transform: rotate(180deg);
    font-family: "Arimo", sans-serif;
    font-size: 28px;
    line-height: 36px;
    color: var(--ink);
    text-align: center;
  }
</style>
</head>
<body>
  <main class="label">
    <div class="rose-art" role="img" aria-label="Illustration of old fashioned pink English roses with buds and leaves"></div>

    <div class="brand-tab">Meadow Crown</div>

    <h1 class="product-name">Rose Petal Jelly</h1>

    <p class="sales-pitch">With whole petals - a taste of summer, delicious<br>on scones, as a filling in sponge cake,<br>as a topping on ice cream or yogurt.</p>

    <div class="net-weight">200g</div>

    <address class="producer" style="font-style: normal;">MEADOW CROWN<br>The Larches, Pardew Lane,<br>Newnham, Gloucestershire<br>GL17 4RX</address>

    <div class="divider"></div>
    <div class="info-band"></div>

    <p class="product-info">INGREDIENTS: Sugar, water, rose petals, lemon juice,<br>natural jelling agent (agar-agar)<br>STORAGE: Store in a cool dry place, once opened keep<br>refrigerated and consume within 4 weeks.</p>

    <p class="best-before">BEST BEFORE:<br>See base</p>

    <div class="barcode-space"><span>BAR<br>CODE</span></div>
  </main>
</body>
</html>
```